Brightline Energy Product Distribution Brochure

We are looking to have our current brochure for our customers completely redesigned...the idea is to present the relevant information in an attractive way . Our website is brightlineenergyco.example where you can find more information about us. We have included a file with a rough idea of the page order and what each should include but feel free to adapt based on design. The example provided is only for context and doesnt have to be maintained. We will be using the brochure both digitally and in print form. As long as it reads easily and is eye catching, the design can be horizontal or vertical.Final deliverable should be indesign file.

"Our Brands" page: should be limited to one page (space being enough) where it has the header for each one (for example diesel generators) space for one or two lines of text and then the corresponding logos for each of the five categories
Updates

For those asking: the "our brands" page should be a single page layout where there is a header with the corresponding section and space for maybe one line of text followed by the two logos for that category. Each of the product pages should be similar in fashion to the one in the document attached: a photo of the product with some white space and space for the text to be included. We will be posting additional examples today

Target Market(s)

We want to present it to customers both digitally and in print so they can see our products

Industry/Entity Type

Power Generation

Font styles to use
Serif

Requirements
Must have
• Eye catching and able to present the information in a presentable fashion. Rest is up to you.
Nice to have
• Should incorporate the colors of our logo but can also add other depending on design

```html
<!DOCTYPE html>
<html lang="en">
<head>
<meta charset="utf-8">
<title>Brightline Energy — Rental Generators &amp; AC Alternators</title>
<link rel="stylesheet" href="https://fonts.googleapis.com/css2?family=Montserrat:wght@300;400;800&display=swap">
<style>
  :root {
    --stage: #d9dad5;
    --paper: #f4f4f4;
    --paper-shade: #e2e2e2;
    --bar: #3a3330;
    --accent: #f2b51c;
    --body-text: #8a8a8a;
    --photo-light: #cfcdca;
    --photo-dark: #6e6a66;
  }
  * { margin: 0; padding: 0; box-sizing: border-box; }
  html, body {
    width: 1200px; height: 960px; overflow: hidden;
    background: var(--stage);
    font-family: "Montserrat", sans-serif;
  }
  .spread {
    position: absolute; left: 30px; top: 250px;
    width: 1140px; height: 460px;
    background: linear-gradient(90deg, var(--paper) 0%, #fafafa 40%, var(--paper-shade) 50%, #fafafa 52%, #ececec 100%);
    box-shadow: 0 14px 40px rgba(0,0,0,.18);
    overflow: hidden;
  }
  .photo-band { position: absolute; inset: 0; }
  .heading-bar {
    position: absolute; height: 66px;
    background: var(--bar);
    display: flex; align-items: center;
  }
  .heading-bar--left { left: 60px; top: 56px; width: 455px; padding-left: 170px; }
  .heading-bar--right { left: 625px; top: 312px; width: 478px; padding-left: 165px; }
  .section-title {
    color: var(--accent); font-weight: 800; font-size: 15px;
    letter-spacing: .02em; text-transform: uppercase; white-space: nowrap;
  }
  .body-copy {
    position: absolute; color: var(--body-text);
    font-weight: 300; font-size: 7.2px; line-height: 1.62;
  }
  .body-copy--left { left: 40px; top: 172px; width: 200px; }
  .body-copy--right { left: 900px; top: 84px; width: 200px; }
  .product {
    position: absolute; border-radius: 4px;
  }
  .product--generator {
    left: 300px; top: 178px; width: 215px; height: 225px;
    background: linear-gradient(160deg, #f6f6f6 0%, #dedede 55%, #2d2d2d 80%, #1a1a1a 100%);
  }
  .product--alternator {
    left: 600px; top: 88px; width: 280px; height: 215px;
    background: radial-gradient(circle at 30% 60%, #8a7a5c 0%, #3a3a3a 35%, #2a2a2a 70%, #4a4a4a 100%);
  }
  .spine {
    position: absolute; left: 568px; top: 0; width: 8px; height: 100%;
    background: linear-gradient(90deg, rgba(0,0,0,0), rgba(0,0,0,.08), rgba(0,0,0,0));
  }
</style>
</head>
<body>
  <main class="spread">
    <svg class="photo-band" width="1140" height="460" viewBox="0 0 1140 460" role="img" aria-label="Greyscale close-up photograph of generator engine components running diagonally across the spread">
      <defs>
        <linearGradient id="band-tone" x1="0" y1="0" x2="1" y2="1">
          <stop offset="0" stop-color="#cfcdca"/>
          <stop offset=".5" stop-color="#6e6a66"/>
          <stop offset="1" stop-color="#cfcdca"/>
        </linearGradient>
      </defs>
      <polygon points="180,0 470,0 1000,460 600,460" fill="url(#band-tone)" opacity=".85"/>
    </svg>

    <div class="heading-bar heading-bar--left"><h2 class="section-title">Rental Generators</h2></div>
    <div class="heading-bar heading-bar--right"><h2 class="section-title">AC Alternators</h2></div>

    <p class="body-copy body-copy--left">Our rental fleet delivers dependable power for construction sites, outdoor events, emergency backup and remote operations. Every unit is trailer mounted, fully serviced and tested before it leaves our yard. Choose from a wide range of sizes to match your load, with fuel efficient engines and quiet enclosures. Our team handles delivery, setup and pickup, so your project stays on schedule. Flexible daily, weekly and monthly terms are available. Contact us to discuss your needs and we will recommend the right generator for the job.</p>

    <p class="body-copy body-copy--right">Our AC alternators are built for continuous duty in standby and prime power applications. Brushless design, class H insulation and precise voltage regulation ensure clean, stable output. Each model is available in single and three phase configurations with a range of mounting options. Robust frames and sealed bearings reduce maintenance and extend service life. We stock replacement units and parts for fast turnaround. Our specialists can help match the alternator to your engine and load profile.</p>

    <div class="product product--generator" role="img" aria-label="Photograph of a white trailer-mounted rental diesel generator"></div>
    <div class="product product--alternator" role="img" aria-label="Photograph of a black AC alternator with exposed coupling disc"></div>

    <div class="spine"></div>
  </main>
</body>
</html>
```